Marlowby Services Website Design

We have most content but require a professional design. We have a logo already and will need it utilized along with several of the photos from the attached documentation.
First page should have our mission and Vision and the synapsis provided in the word document. Visitors will be prompted to select from one of our 3 divisions from this page.
Each division will have the same list of tabs : About, Services, Safety, Careers and Contact.
Photos on each divisions page should be representative of the divisions offerings. The word doc attached contains the requested content and we are open to edits that would complement and fill the website.
I like the Quorvane site www.quorvane.example - they are our competition so cant be modeled directly after this.
Please include prompts to request quote at each service page. align the format of the geotechnical page to the other 2 divisions.
I used chat gpt for some of the content so will need it optimized for SCO.

```html
<!DOCTYPE html>
<html lang="en">
<head>
<meta charset="utf-8">
<title>Marlowby Services</title>
<link rel="stylesheet" href="https://fonts.googleapis.com/css2?family=Michroma&family=Oswald:wght@500&family=Lato:wght@400;700&display=swap">
<style>
:root{
  --red:#e31e24;
  --ink:#1f1f1f;
  --body:#3a3a3a;
  --white:#ffffff;
  --night:#0b1a33;
  --steel:#1d4f8f;
  --footer:#1c1c1e;
}
*{box-sizing:border-box;margin:0;padding:0}
html,body{width:1200px;height:3234px;overflow:hidden;background:var(--white)}
body{position:relative;font-family:"Lato",sans-serif;color:var(--ink)}
.abs{position:absolute}
.brand{font-family:"Michroma",sans-serif;color:var(--red);letter-spacing:2px;font-size:30px;line-height:1}
.heading{font-family:"Michroma",sans-serif;color:var(--red);font-size:33px;letter-spacing:1px;line-height:1}
.btn{position:absolute;background:var(--red);color:var(--white);font-size:15px;display:flex;align-items:center;justify-content:center}

/* header */
.site-header{left:0;top:0;width:1200px;height:63px;background:var(--white)}
.site-header .brand{left:140px;top:15px}
.main-nav a{position:absolute;top:22px;font-size:13px;color:var(--ink);text-decoration:none}

/* hero */
.hero{left:0;top:63px;width:1200px;height:600px;background:linear-gradient(100deg,#07101f 0%,#0c2346 45%,#1b4f95 75%,#2a6dbf 100%)}
.hero-title{left:145px;top:245px;font-family:"Oswald",sans-serif;font-weight:500;font-size:48px;line-height:54px;color:var(--white)}
.hero-sub{left:143px;top:418px;font-size:20px;line-height:27px;color:var(--white);font-weight:700;width:450px}

/* divisions */
.division{position:absolute;top:813px;width:283px;height:314px;overflow:hidden}
.division h3{position:absolute;font-family:"Michroma",sans-serif;font-size:14px;font-weight:400;color:var(--white);letter-spacing:.5px;line-height:18px}
.division p{position:absolute;left:19px;top:202px;width:250px;font-size:11.5px;line-height:20px;color:var(--white)}
.go{position:absolute;width:20px;height:20px}

/* about */
.about-text{left:631px;width:424px;font-size:13px;line-height:21.8px;color:var(--body);letter-spacing:.15px}
.about-text b{color:var(--ink)}

/* services */
.service{position:absolute;top:1933px;width:212px;height:226px;background:var(--white);box-shadow:0 4px 10px rgba(0,0,0,.12);text-align:center}
.service svg{position:absolute;left:78px;top:34px}
.service h3{position:absolute;left:0;right:0;top:106px;font-family:"Michroma",sans-serif;font-weight:400;font-size:15px;line-height:17px;color:var(--ink)}
.service p{position:absolute;left:10px;right:10px;font-size:12.5px;line-height:20px;color:var(--body)}

/* footer */
.site-footer{left:0;top:2843px;width:1200px;height:391px;background:linear-gradient(180deg,#2a2a2c 0%,#1b1c20 55%,#3a3226 100%)}
.footer-rule{position:absolute;left:140px;width:922px;height:1px;background:rgba(255,255,255,.25)}
.footer-nav a{position:absolute;top:168px;font-size:13px;color:var(--white);text-decoration:none}
.contact-item{position:absolute;top:262px;color:var(--white);font-size:12.5px;line-height:20px}
.contact-item .label{font-family:"Michroma",sans-serif;font-size:12.5px}
.contact-icon{position:absolute;top:264px}
.copyright{position:absolute;left:0;right:0;top:352px;text-align:center;font-size:11.5px;color:var(--white)}
</style>
</head>
<body>

<header class="abs site-header">
  <div class="abs brand">MARLOWBY</div>
  <nav class="main-nav">
    <a style="left:639px">About</a>
    <a style="left:710px">Services</a>
    <a style="left:796px">Safety</a>
    <a style="left:868px">Careers</a>
  </nav>
  <div class="btn" style="left:937px;top:13px;width:117px;height:33px">Contact Us</div>
</header>

<section class="abs hero" role="img" aria-label="Industrial refinery lit at night with towers and pipework"></section>
<h1 class="abs hero-title">Delivering Safe,<br>Reliable Aerial Access<br>&amp; Maintenance Services</h1>
<p class="abs hero-sub">To Oil &amp; Gas,Construction, Utility, &amp; Renewable Energy Sector</p>
<div class="btn" style="left:141px;top:489px;width:117px;height:34px">Contact Us</div>

<h2 class="abs heading" style="left:0;width:1200px;text-align:center;top:719px">OUR DIVISIONS</h2>

<article class="division" style="left:139px;background:linear-gradient(180deg,#2a5a9c 0%,#3f79bd 55%,#1b2a3a 100%)" role="img" aria-label="Aerial lift boom beside a wind turbine tower">
  <h3 style="left:16px;top:177px">Aerial Access</h3>
  <p>Marlowby is a full-service wind energy service provider specializing in blade access &amp; repair , service and maintenance , &amp; trouble shooting on most wind turbine platforms.</p>
  <svg class="go" style="left:249px;top:273px" viewBox="0 0 20 20"><circle cx="10" cy="10" r="10" fill="var(--red)"/><path d="M5.5 10h8M10.5 6.5 14 10l-3.5 3.5" stroke="#fff" stroke-width="1.4" fill="none"/></svg>
</article>
<article class="division" style="left:458px;background:linear-gradient(180deg,#1d3a2a 0%,#2f5a3a 55%,#324a2a 100%)" role="img" aria-label="Red tracked drilling rig in a forest clearing">
  <h3 style="left:17px;top:274px">Geotechnical Drilling</h3>
  <svg class="go" style="left:238px;top:273px" viewBox="0 0 20 20"><circle cx="10" cy="10" r="10" fill="var(--red)"/><path d="M5.5 10h8M10.5 6.5 14 10l-3.5 3.5" stroke="#fff" stroke-width="1.4" fill="none"/></svg>
</article>
<article class="division" style="left:777px;background:linear-gradient(180deg,#1c5fae 0%,#2466b5 50%,#123a73 100%)" role="img" aria-label="Wind turbine against a deep blue sky">
  <h3 style="left:19px;top:262px">Renewable Energy<br>Services</h3>
  <svg class="go" style="left:238px;top:273px" viewBox="0 0 20 20"><circle cx="10" cy="10" r="10" fill="var(--red)"/><path d="M5.5 10h8M10.5 6.5 14 10l-3.5 3.5" stroke="#fff" stroke-width="1.4" fill="none"/></svg>
</article>

<div class="abs" style="left:0;top:1255px;width:582px;height:498px;background:linear-gradient(180deg,#3d5a45 0%,#c9ccd0 45%,#8a8780 100%)" role="img" aria-label="White aerial lift truck parked on gravel"></div>
<h2 class="abs heading" style="left:634px;top:1330px">ABOUT MARLOWBY</h2>
<div class="abs about-text" style="top:1377px">
  <p style="margin-bottom:5px"><b>Our Vision</b> to be the leading provider of aerial access, geotechnical drilling, and service solutions, setting the standard for excellence in safety, efficiency, and environmental stewardship.</p>
  <p><b>Our Mission</b> at Marlowby, our mission is to deliver unparalleled aerial access, geotechnical drilling, and service &amp; maintenance solutions, consistently exceeding our clients' expectations. We strive to achieve this by investing in cutting-edge technology, fostering a culture of safety &amp; continuous improvement, &amp; prioritizing environmental sustainability. Through collaboration, integrity, and dedication, we aim to contribute to the success of our clients while maintaining the highest standards of quality and professionalism.</p>
</div>
<div class="btn" style="left:630px;top:1639px;width:117px;height:34px">Read More</div>

<h2 class="abs heading" style="left:0;width:1200px;text-align:center;top:1840px">OUR SERVICES</h2>
<p class="abs" style="left:0;width:1200px;text-align:center;top:1889px;font-size:15px;color:var(--ink)">Delivering safe, reliable aerial access and maintenance services</p>

<article class="service" style="left:146px">
  <svg width="56" height="56" viewBox="0 0 56 56"><circle cx="28" cy="28" r="28" fill="var(--red)"/><g stroke="#fff" stroke-width="1.6" fill="none"><rect x="19" y="18" width="18" height="21"/><path d="M23 23h3M30 23h3M23 28h3M30 28h3M26 39v-6h4v6"/></g></svg>
  <h3>Oil&amp;Gas</h3>
  <p style="top:136px">Lorem ipsum dolor sit amet, consectetur adipiscing elit, sed do eiusmod tempor incididunt</p>
</article>
<article class="service" style="left:378px">
  <svg width="56" height="56" viewBox="0 0 56 56"><circle cx="28" cy="28" r="28" fill="var(--red)"/><g stroke="#fff" stroke-width="1.6" fill="none"><path d="M22 40l6-24 6 24M18 18h20M24 31h8M20 40h16"/></g></svg>
  <h3>Construction</h3>
  <p style="top:136px">Lorem ipsum dolor sit amet, consectetur adipiscing elit, sed do eiusmod tempor incididunt</p>
</article>
<article class="service" style="left:610px">
  <svg width="56" height="56" viewBox="0 0 56 56"><circle cx="28" cy="28" r="28" fill="var(--red)"/><g stroke="#fff" stroke-width="1.6" fill="none"><circle cx="28" cy="28" r="5"/><path d="M28 16v5M28 35v5M16 28h5M35 28h5M19.5 19.5l3.5 3.5M33 33l3.5 3.5M36.5 19.5 33 23M23 33l-3.5 3.5"/></g></svg>
  <h3>Utility</h3>
  <p style="top:136px">Lorem ipsum dolor sit amet, consectetur adipiscing elit, sed do eiusmod tempor incididunt</p>
</article>
<article class="service" style="left:843px">
  <svg width="56" height="56" viewBox="0 0 56 56"><circle cx="28" cy="28" r="28" fill="var(--red)"/><g stroke="#fff" stroke-width="1.6" fill="none"><path d="M24 40V24M24 24l-6-5M24 24l7-3M24 24l-1 8M30 40V30h8v10M32 33h4"/></g></svg>
  <h3>Renewable Energy<br>Industries</h3>
  <p style="top:152px">consectetur adipiscing elit sed do eiusmod tempor incididunt</p>
</article>

<h2 class="abs heading" style="left:143px;top:2418px">WHY CHOOSE US</h2>
<p class="abs" style="left:143px;top:2465px;width:430px;font-size:15.5px;line-height:26.5px;color:var(--ink)"><span style="color:var(--red)">MARLOWBY</span> Is A Full-service Wind Energy Service Provider Specializing In Blade Access &amp; Repair, Service &amp; Maintenance, And Trouble Shooting On Most Wind Turbine Platforms.</p>
<div class="btn" style="left:141px;top:2553px;width:117px;height:34px">Contact Us</div>
<div class="abs" style="left:612px;top:2253px;width:588px;height:498px;background:linear-gradient(180deg,#5f7a3a 0%,#8ea35a 35%,#d8d8d4 55%,#6c6350 100%)" role="img" aria-label="Aerial lift truck parked in a wooded yard"></div>

<footer class="abs site-footer" role="img" aria-label="Dark city skyline at dusk behind footer content">
  <div class="brand" style="position:absolute;left:0;width:1200px;text-align:center;top:56px">MARLOWBY</div>
  <div class="footer-rule" style="top:131px"></div>
  <nav class="footer-nav">
    <a style="left:322px">Home</a>
    <a style="left:414px">About</a>
    <a style="left:506px">Services</a>
    <a style="left:611px">Safety</a>
    <a style="left:704px">Careers</a>
    <a style="left:807px;font-size:14px">Contact Us</a>
  </nav>
  <div class="footer-rule" style="top:223px"></div>

  <svg class="contact-icon" style="left:199px" width="29" height="29" viewBox="0 0 29 29"><circle cx="14.5" cy="14.5" r="13.5" stroke="#fff" stroke-width="1.3" fill="none"/><path d="M14.5 8.5a4 4 0 0 0-4 4c0 3 4 7.5 4 7.5s4-4.5 4-7.5a4 4 0 0 0-4-4z" fill="#fff"/><circle cx="14.5" cy="12.5" r="1.4" fill="#1c1c1e"/></svg>
  <div class="contact-item" style="left:236px">118 Ridgeway Road Alder Flats<br>AB T0A-1K0</div>

  <svg class="contact-icon" style="left:526px" width="29" height="29" viewBox="0 0 29 29"><circle cx="14.5" cy="14.5" r="13.5" stroke="#fff" stroke-width="1.3" fill="none"/><path d="M10.5 9l2.5-.5 1.3 3-1.5 1.2a7 7 0 0 0 3.5 3.5l1.2-1.5 3 1.3-.5 2.5c-5 .5-10-4.5-9.5-9.5z" fill="#fff"/></svg>
  <div class="contact-item" style="left:567px"><span class="label">Phone</span><br>(555)-014-7392</div>

  <svg class="contact-icon" style="left:792px" width="29" height="29" viewBox="0 0 29 29"><circle cx="14.5" cy="14.5" r="13.5" stroke="#fff" stroke-width="1.3" fill="none"/><rect x="9" y="10.5" width="11" height="8" fill="#fff"/><path d="M9 10.5l5.5 4.5 5.5-4.5" stroke="#1c1c1e" stroke-width="1.1" fill="none"/></svg>
  <div class="contact-item" style="left:832px"><span class="label">Email</span><br>career@marlowbyservices.example</div>

  <p class="copyright">© 2024 <b>MARLOWBY</b>. All Rights Reserved.</p>
</footer>

</body>
</html>
```